Reach Crafters Unique Marketing Website Design

I am starting a new company that is a thought leader in the marketing consulting space. The company is called Reach Crafters. We intend to build a Wordpress site on the Astra Theme with the Spectra builder. Our goal is to become the leading voice that empowers high-ticket service business leaders to become Reach Crafters by equipping them with the cutting-edge frameworks and decision grade intelligence taught in leading business schools. What we are looking for is a website design that is clean and professional, making some use of white space well also being eye catching and distinctive in the consulting space. We will probably want to have a video on the homepage not in the hero section, but just below to explain the company and what we do. Our tagline is "Be found. Be chosen." I have attached a brand guide with some messaging, our typography choices, and our color system. The full site will have a primary nav that is four pages - About us, Services, Insights (essentially a blog), and Contact Us. The goal of this project is to develop an art direction that I can give to a designer to build loads of new pages.

Target Market(s)

Business owners (mostly male) from 30-60 years old, looking to fix their sales and marketing funnel.

Industry/Entity Type

Marketing consulting

Font styles to use
Sans Serif

Requirements
Must have
• A clean, professional design that builds trust with owners of high-ticket service businesses. We need a space for explainer video, and sections that tell prospects what we do. Would also like to have a blog carousel.
Nice to have
• Social feeds, if possible. See attached documents for colors and fonts.
Should not have
• Our feel is professional enough to be trustworthy, but unique enough to be memorable. Cartoon ideas do not meet the professional test, and we do not want the website to appear feminine.

```html
<!DOCTYPE html>
<html lang="en">
<head>
<meta charset="utf-8">
<title>Reach Crafters — Be Found. Be Chosen.</title>
<link href="https://fonts.googleapis.com/css2?family=Oswald:wght@500;600;700&family=Inter:wght@400;500;600;700&display=swap" rel="stylesheet">
<style>
:root{
  --navy:#0d1b3e;
  --navy-deep:#081330;
  --blue:#1e5eff;
  --green:#17a35c;
  --red:#e53935;
  --purple:#7a3fe0;
  --ink:#1b1f2a;
  --muted:#5b6070;
  --grey:#e9eaee;
  --card:#efeff2;
  --white:#ffffff;
}
*{margin:0;padding:0;box-sizing:border-box}
html,body{width:1200px;height:3924px;overflow:hidden}
body{font-family:"Inter",Arial,sans-serif;color:var(--ink);background:var(--white);position:relative}
.heading{font-family:"Oswald","Arial Narrow",sans-serif;font-weight:700;text-transform:uppercase;line-height:1.05;color:var(--navy)}
.accent{color:var(--blue)}
.label{font-size:13px;color:var(--muted);display:flex;align-items:center;gap:8px}
.label::before{content:"";width:24px;height:2px;background:var(--green)}
.center .label{justify-content:center}
.btn{display:inline-block;font-size:13px;font-weight:600;color:#fff;padding:12px 22px;border-radius:3px}
.btn-green{background:var(--green)}
.btn-red{background:var(--red)}
.btn-navy{background:var(--navy)}
.media{position:absolute;display:block}
.abs{position:absolute}

/* Header */
.site-header{position:absolute;left:0;top:0;width:1200px;height:88px;background:#fff;z-index:3}
.brand{position:absolute;left:40px;top:18px}
.brand-name{font-family:"Oswald",sans-serif;font-weight:700;font-size:26px;color:var(--navy);letter-spacing:.5px;display:flex;align-items:center;gap:10px}
.brand-name .mark{width:12px;height:12px;background:var(--green)}
.brand-tag{font-size:12px;color:var(--muted);margin-top:2px}
.contact-strip{position:absolute;left:590px;top:22px;display:flex;gap:30px;font-size:12px}
.contact-strip .item{display:flex;gap:8px;align-items:center}
.contact-strip small{display:block;color:var(--muted);font-size:11px}
.contact-strip b{color:var(--navy);font-size:14px}
.header-cta{position:absolute;right:40px;top:22px}
.main-nav{position:absolute;left:140px;top:88px;width:860px;height:36px;background:var(--navy);display:flex;align-items:center;padding-left:40px;gap:36px;z-index:3}
.main-nav a{color:#fff;font-size:12px;font-weight:600;text-transform:uppercase}
.main-nav a.active{color:var(--green)}
.nav-social{position:absolute;left:1010px;top:94px;display:flex;gap:8px;z-index:3}
.nav-social span{width:24px;height:24px;background:var(--navy);border-radius:3px}

/* Hero */
.hero{position:absolute;left:0;top:0;width:1200px;height:680px;background:linear-gradient(90deg,#f2f3f5 0%,#eceef1 50%,#dfe3e8 100%)}
.hero-photo{left:560px;top:88px;width:640px;height:592px;background:linear-gradient(160deg,#b9c2cc 0%,#5d6b7d 45%,#2a3446 100%)}
.hero-copy{position:absolute;left:140px;top:240px;width:420px}
.hero-title{font-size:84px;line-height:.98;color:var(--navy-deep)}
.hero-text{font-size:16px;line-height:1.55;color:var(--ink);margin-top:24px;font-weight:500}
.hero-actions{margin-top:26px;display:flex;gap:12px}

/* About */
.about{position:absolute;left:0;top:680px;width:1200px;height:560px;background:#fff}
.video-frame{position:absolute;left:170px;top:80px;width:390px;height:370px}
.video-accent{position:absolute;left:-14px;top:40px;width:390px;height:350px;background:var(--green)}
.video-still{left:0;top:0;width:390px;height:360px;background:linear-gradient(135deg,#3b4d6b 0%,#1c2a47 60%,#0d1b3e 100%)}
.play{position:absolute;left:165px;top:150px}
.about-copy{position:absolute;left:640px;top:90px;width:440px}
.about-copy .heading{font-size:44px;margin-top:14px}
.about-copy p{font-size:14px;line-height:1.6;color:var(--muted);margin-top:16px}
.about-copy p.lead{color:var(--blue);font-weight:500}
.about-copy p.sign{color:var(--navy);font-weight:700}
.about-copy .btn{margin-top:24px}

/* Services */
.services{position:absolute;left:0;top:1260px;width:1200px;height:760px;background:var(--grey)}
.section-head{position:absolute;left:0;width:1200px;text-align:center}
.section-head .heading{font-size:46px;margin-top:12px}
.service-grid{position:absolute;left:140px;top:230px;display:flex;gap:20px}
.service{width:215px}
.service-img{position:relative;width:215px;height:220px}
.service h3{font-size:14px;font-weight:700;color:var(--navy);margin-top:14px}
.service p{font-size:12px;line-height:1.55;color:var(--muted);margin-top:6px}
.services .more{position:absolute;left:545px;top:590px}

/* Testimonials */
.testimonials{position:absolute;left:0;top:2060px;width:1200px;height:420px}
.quote-grid{position:absolute;left:140px;top:140px;display:flex;gap:25px}
.quote{position:relative;width:290px;height:220px;background:var(--card);padding:30px 26px 22px}
.quote .qmark{position:absolute;right:-8px;top:-14px}
.quote p{font-size:13px;line-height:1.6;color:var(--muted)}
.quote .who{margin-top:18px;font-size:13px;color:var(--blue);font-weight:600}
.quote .role{font-size:11px;color:var(--muted)}
.pager{position:absolute;left:560px;top:340px;display:flex;gap:10px}
.pager span{width:34px;height:34px;display:flex;align-items:center;justify-content:center;border:1px solid var(--navy)}
.pager span.on{background:var(--green);border-color:var(--green)}

/* Blog */
.blog{position:absolute;left:0;top:2520px;width:1200px;height:400px}
.blog-intro{position:absolute;left:130px;top:40px;width:240px}
.blog-intro .heading{font-size:48px;margin-top:12px}
.blog-intro p{font-size:14px;line-height:1.55;color:var(--muted);margin-top:14px}
.blog-intro .btn{margin-top:22px}
.posts{position:absolute;left:400px;top:40px;display:flex;gap:14px}
.post{width:185px}
.post-img{position:relative;width:185px;height:160px}
.tag{position:absolute;left:8px;bottom:-10px;background:var(--green);color:#fff;font-size:10px;font-weight:600;padding:4px 8px}
.post h4{font-size:14px;font-weight:700;color:var(--navy);margin-top:22px;line-height:1.3}
.post p{font-size:11px;line-height:1.5;color:var(--muted);margin-top:6px}
.meta{display:flex;gap:12px;font-size:10px;color:var(--muted);margin-top:10px}
.meta i{display:inline-block;width:8px;height:8px;background:var(--red);margin-right:4px;font-style:normal}

/* CTA */
.cta{position:absolute;left:0;top:2960px;width:1200px;height:640px}
.cta-bg{left:0;top:0;width:1200px;height:640px;background:linear-gradient(180deg,#1d2b48 0%,#0b1730 60%,#071126 100%)}
.cta .section-head .heading{color:#fff;font-size:52px}
.cta-text{font-size:15px;color:#d9deea;margin-top:16px;line-height:1.5;font-weight:500}
.cta-boxes{position:absolute;left:228px;top:370px;display:flex;gap:60px}
.cta-box{width:200px;height:220px;color:#fff;text-align:center;padding:42px 18px 0}
.cta-box h5{font-size:17px;font-weight:700;line-height:1.35}
.cta-box .btn{margin-top:22px;font-size:12px;padding:10px 18px}
.box-blue{background:var(--blue)}
.box-blue .btn{background:var(--navy)}
.box-red{background:var(--red)}
.box-red .btn{background:var(--green)}
.box-purple{background:var(--purple)}
.box-purple .btn{background:var(--navy)}

/* Footer */
.site-footer{position:absolute;left:0;top:3600px;width:1200px;height:260px;background:#fff}
.foot-col{position:absolute;top:50px}
.foot-col h6{font-family:"Oswald",sans-serif;font-size:18px;font-weight:600;text-transform:uppercase;color:var(--navy)}
.foot-col h6 span{color:var(--red)}
.foot-col p,.foot-col li{font-size:12px;line-height:1.6;color:var(--muted)}
.foot-col ul{list-style:none;margin-top:12px}
.foot-col li{display:flex;align-items:center;gap:8px}
.foot-col li::before{content:"";width:5px;height:5px;background:var(--green)}
.foot-contact li::before{display:none}
.news-input{margin-top:12px;width:190px;height:34px;border:1px solid #cfd3da;font-size:12px;color:#9aa0ad;padding:9px 10px}
.news-btn{margin-top:10px;width:120px;background:var(--red);color:#fff;font-size:12px;font-weight:600;text-align:center;padding:10px 0}
.foot-bar{position:absolute;left:0;top:3860px;width:1200px;height:64px;background:var(--navy-deep);color:#cfd5e2;font-size:12px;padding:0 140px;display:flex;align-items:center;justify-content:space-between}
.foot-bar .socials{display:flex;gap:8px}
.foot-bar .socials span{width:24px;height:24px;background:#2a3a60;border-radius:3px}
</style>
</head>
<body>

<section class="hero">
  <div class="media hero-photo" role="img" aria-label="Photo of two businessmen in suits talking in a modern office"></div>
  <div class="hero-copy">
    <h1 class="heading hero-title">Be Found.<br>Be Chosen.</h1>
    <p class="hero-text">Empowering high-ticket service business leaders with cutting-edge marketing frameworks and decision-grade intelligence to dominate their sales funnels.</p>
    <div class="hero-actions">
      <span class="btn btn-red">Explore Our Services</span>
      <span class="btn btn-navy">Schedule a Consultation</span>
    </div>
  </div>
</section>

<header class="site-header">
  <div class="brand">
    <div class="brand-name"><span class="mark"></span>REACH CRAFTERS</div>
    <div class="brand-tag">Be Found. Be Chosen.</div>
  </div>
  <div class="contact-strip">
    <div class="item">
      <svg width="22" height="22" viewBox="0 0 24 24"><circle cx="12" cy="12" r="12" fill="#17a35c"/><path d="M8 6l2 0 1 3-1.5 1a7 7 0 0 0 4.5 4.5l1-1.5 3 1v2a2 2 0 0 1-2 2A10 10 0 0 1 6 8a2 2 0 0 1 2-2z" fill="#fff"/></svg>
      <div><small>Phone Us</small><b>(555) 014-2290</b></div>
    </div>
    <div class="item">
      <svg width="22" height="22" viewBox="0 0 24 24"><circle cx="12" cy="12" r="12" fill="#17a35c"/><rect x="6" y="8" width="12" height="8" fill="none" stroke="#fff" stroke-width="1.6"/><path d="M6 8l6 5 6-5" fill="none" stroke="#fff" stroke-width="1.6"/></svg>
      <div><small>Email</small><b style="font-size:12px">hello@reachcrafters.example</b></div>
    </div>
  </div>
  <span class="btn btn-green header-cta">Schedule a Consultation</span>
</header>

<nav class="main-nav">
  <a class="active">Home</a><a>About Us</a><a>Services</a><a>Insights</a><a>Contact Us</a>
</nav>
<div class="nav-social"><span></span><span></span><span></span><span></span></div>

<section class="about">
  <div class="video-frame">
    <div class="video-accent"></div>
    <div class="media video-still" role="img" aria-label="Explainer video still of a consultant presenting to a client"></div>
    <svg class="play" width="60" height="60" viewBox="0 0 60 60"><circle cx="30" cy="30" r="30" fill="#e53935"/><path d="M24 19l18 11-18 11z" fill="#fff"/></svg>
  </div>
  <div class="about-copy">
    <div class="label">About Reach Crafters</div>
    <h2 class="heading">Build Your Business<br><span class="accent">With Right Way</span></h2>
    <p class="lead">At Reach Crafters, we help business owners turn marketing into a predictable growth engine.</p>
    <p>Too many owners of high-ticket service firms rely on referrals and luck. We bring proven frameworks and clear data so every lead, call and proposal moves with purpose toward a signed client.</p>
    <p>Reach Crafters is a consulting firm built for founders and CEOs who want clarity, control and consistent demand. We specialise in diagnosing and optimising the entire sales and marketing funnel, from positioning and messaging to lead generation, conversion and revenue alignment.</p>
    <p class="sign">Reach Crafters. Build demand. Drive growth.</p>
    <span class="btn btn-green">Read More</span>
  </div>
</section>

<section class="services">
  <div class="section-head center" style="top:70px">
    <div class="label">Services</div>
    <h2 class="heading">Empowering Business<br><span class="accent">Leaders Like You</span></h2>
  </div>
  <div class="service-grid">
    <div class="service">
      <div class="media service-img" style="position:relative;background:linear-gradient(135deg,#1a1f2e,#3d4a6a)" role="img" aria-label="Photo of a sales funnel diagram on a dark screen"></div>
      <h3>Funnel Optimization</h3>
      <p>Analyze and optimize your entire sales and marketing funnel to increase conversion rates and revenue per lead.</p>
    </div>
    <div class="service">
      <div class="media service-img" style="position:relative;background:linear-gradient(135deg,#6f7e96,#2c3a55)" role="img" aria-label="Photo of a team reviewing demand generation plans"></div>
      <h3>Demand Generation</h3>
      <p>Implement cutting-edge demand generation strategies that attract high-value clients and position your business as the leader.</p>
    </div>
    <div class="service">
      <div class="media service-img" style="position:relative;background:linear-gradient(135deg,#1c2b25,#4e6f5e)" role="img" aria-label="Photo of a hand selecting a rating on a screen"></div>
      <h3>High-Ticket Positioning</h3>
      <p>Develop premium positioning strategies that allow you to command higher prices and attract clients who value your expertise.</p>
    </div>
    <div class="service">
      <div class="media service-img" style="position:relative;background:linear-gradient(135deg,#c9ced6,#6c7688)" role="img" aria-label="Photo of an executive presenting at a training session"></div>
      <h3>Executive Training</h3>
      <p>Equip your leadership team with the business school frameworks and intelligence to make data-driven marketing decisions.</p>
    </div>
  </div>
  <span class="btn btn-green more">View All Services</span>
</section>

<section class="testimonials">
  <div class="section-head center" style="top:40px">
    <div class="label">Testimonials</div>
    <h2 class="heading">What <span class="accent">Our Clients</span> Say</h2>
  </div>
  <div class="quote-grid">
    <div class="quote">
      <svg class="qmark" width="36" height="36" viewBox="0 0 36 36"><rect width="36" height="36" fill="#e53935"/><path d="M9 24v-6c0-4 2-7 6-8v3c-2 1-3 2-3 4h3v7zM20 24v-6c0-4 2-7 6-8v3c-2 1-3 2-3 4h3v7z" fill="#fff"/></svg>
      <p>The frameworks provided by Reach Crafters transformed our approach to client acquisition. We've increased our average deal size by 45% while reducing acquisition costs.</p>
      <div class="who">Daniel Ortega</div>
      <div class="role">Founder, Northfield Advisory</div>
    </div>
    <div class="quote">
      <svg class="qmark" width="36" height="36" viewBox="0 0 36 36"><rect width="36" height="36" fill="#e53935"/><path d="M9 24v-6c0-4 2-7 6-8v3c-2 1-3 2-3 4h3v7zM20 24v-6c0-4 2-7 6-8v3c-2 1-3 2-3 4h3v7z" fill="#fff"/></svg>
      <p>Reach Crafters helped us identify critical leaks in our funnel that we never knew existed. Our close rate has improved by 300% in just 90 days.</p>
      <div class="who">Karen Whitfield</div>
      <div class="role">CEO, Summit Legal Group</div>
    </div>
    <div class="quote">
      <svg class="qmark" width="36" height="36" viewBox="0 0 36 36"><rect width="36" height="36" fill="#e53935"/><path d="M9 24v-6c0-4 2-7 6-8v3c-2 1-3 2-3 4h3v7zM20 24v-6c0-4 2-7 6-8v3c-2 1-3 2-3 4h3v7z" fill="#fff"/></svg>
      <p>Working with Reach Crafters gave us the clarity and systems we needed to scale efficiently. Their intelligence reports alone have paid for the engagement ten times over.</p>
      <div class="who">Priya Nolan</div>
      <div class="role">Managing Director, Brightline Systems</div>
    </div>
  </div>
  <div class="pager">
    <span><svg width="12" height="12" viewBox="0 0 12 12"><path d="M8 1L3 6l5 5" fill="none" stroke="#0d1b3e" stroke-width="2"/></svg></span>
    <span class="on"><svg width="12" height="12" viewBox="0 0 12 12"><path d="M4 1l5 5-5 5" fill="none" stroke="#fff" stroke-width="2"/></svg></span>
  </div>
</section>

<section class="blog">
  <div class="blog-intro">
    <div class="label">Blog &amp; News</div>
    <h2 class="heading">Latest<br><span class="accent">Insights</span></h2>
    <p>Stay ahead with our thought leadership content on marketing strategy, funnel optimization, and demand generation for high-ticket services.</p>
    <span class="btn btn-green">View All Insights</span>
  </div>
  <div class="posts">
    <div class="post">
      <div class="media post-img" style="position:relative;background:linear-gradient(135deg,#8796ac,#2f3d58)" role="img" aria-label="Photo of a businessman on a phone call"><span class="tag">Marketing</span></div>
      <h4>How to 3x Your Lead Quality in 90 Days</h4>
      <p>Proven tactics from top consultants that help you attract premium clients and eliminate time-wasters.</p>
      <div class="meta"><span><i></i>28 Jan, 2026</span><span><i></i>Comments (5)</span></div>
    </div>
    <div class="post">
      <div class="media post-img" style="position:relative;background:linear-gradient(135deg,#c7cdd6,#56637a)" role="img" aria-label="Photo of a team meeting around a table"><span class="tag">Branding</span></div>
      <h4>How to 3x Your Lead Quality in 90 Days</h4>
      <p>Proven tactics from top consultants that help you attract premium clients and eliminate time-wasters.</p>
      <div class="meta"><span><i></i>28 Jan, 2026</span><span><i></i>Comments (5)</span></div>
    </div>
    <div class="post">
      <div class="media post-img" style="position:relative;background:linear-gradient(135deg,#d3d8de,#6e7a8e)" role="img" aria-label="Photo of colleagues working on laptops"><span class="tag">Strategy</span></div>
      <h4>How to 3x Your Lead Quality in 90 Days</h4>
      <p>Proven tactics from top consultants that help you attract premium clients and eliminate time-wasters.</p>
      <div class="meta"><span><i></i>28 Jan, 2026</span><span><i></i>Comments (5)</span></div>
    </div>
    <div class="post">
      <div class="media post-img" style="position:relative;background:linear-gradient(135deg,#9aa6b6,#394761)" role="img" aria-label="Photo of a consultant presenting to a board"><span class="tag">Consulting</span></div>
      <h4>How to 3x Your Lead Quality in 90 Days</h4>
      <p>Proven tactics from top consultants that help you attract premium clients and eliminate time-wasters.</p>
      <div class="meta"><span><i></i>28 Jan, 2026</span><span><i></i>Comments (5)</span></div>
    </div>
  </div>
</section>

<section class="cta">
  <div class="media cta-bg" role="img" aria-label="Dark photo of a city skyline at dusk behind a blue overlay"></div>
  <div class="section-head center" style="top:120px">
    <h2 class="heading">Ready to Transform<br>Your Demand Generation?</h2>
    <p class="cta-text">Join hundreds of high-ticket service business leaders who have increased their lead quality,<br>conversion rates, and average deal size with our proven frameworks.</p>
    <span class="btn btn-green" style="margin-top:24px">Schedule Your Strategy Call Now</span>
  </div>
  <div class="cta-boxes">
    <div class="cta-box box-blue"><h5>Let's Ready to Get Work Together</h5><span class="btn">Contact Us</span></div>
    <div class="cta-box box-red"><h5>Request to Call Back We Will Call!</h5><span class="btn">Schedule a Consultation</span></div>
    <div class="cta-box box-purple"><h5>Build A Better Career With Reach Crafters</h5><span class="btn">Join Now</span></div>
  </div>
</section>

<footer class="site-footer">
  <div class="foot-col" style="left:140px;width:200px">
    <div class="brand-name" style="font-size:22px">REACH CRAFTERS</div>
    <div class="brand-tag">Be Found. Be Chosen.</div>
    <p style="margin-top:12px">Empowering high-ticket service business leaders with cutting-edge marketing frameworks and decision-grade intelligence to dominate their sales funnels.</p>
  </div>
  <div class="foot-col" style="left:420px">
    <h6>Quick <span>Links</span></h6>
    <ul><li>Home</li><li>About Us</li><li>Services</li><li>Insights</li><li>Contact Us</li></ul>
  </div>
  <div class="foot-col foot-contact" style="left:620px;width:200px">
    <h6>Contact <span>Details</span></h6>
    <ul>
      <li><svg width="14" height="14" viewBox="0 0 24 24"><path d="M12 2a7 7 0 0 0-7 7c0 5 7 13 7 13s7-8 7-13a7 7 0 0 0-7-7zm0 9.5A2.5 2.5 0 1 1 12 6.5a2.5 2.5 0 0 1 0 5z" fill="#0d1b3e"/></svg>48 Harbor Lane, Suite 210</li>
      <li><svg width="14" height="14" viewBox="0 0 24 24"><path d="M6 3l4 0 2 5-2.5 1.5a11 11 0 0 0 5 5L16 12l5 2v4a2 2 0 0 1-2 2A17 17 0 0 1 4 5a2 2 0 0 1 2-2z" fill="#0d1b3e"/></svg>(555) 014-2290</li>
      <li><svg width="14" height="14" viewBox="0 0 24 24"><rect x="3" y="5" width="18" height="14" fill="none" stroke="#0d1b3e" stroke-width="2"/><path d="M3 5l9 7 9-7" fill="none" stroke="#0d1b3e" stroke-width="2"/></svg>hello@reachcrafters.example</li>
    </ul>
  </div>
  <div class="foot-col" style="left:860px;width:200px">
    <h6>News<span>letter</span></h6>
    <p style="margin-top:10px">Subscribe to our newsletter to get the latest update to your inbox.</p>
    <div class="news-input">Email Address</div>
    <div class="news-btn">SUBSCRIBE</div>
  </div>
</footer>
<div class="foot-bar">
  <span>© 2026 REACH CRAFTERS. All Rights Reserved.</span>
  <div class="socials"><span></span><span></span><span></span><span></span></div>
</div>

</body>
</html>
```